Logo + Label Design (Men’s Grooming Brand & Product Packaging)

Design a logo and 2 oz pomade label for Brel, a modern men’s grooming brand focused on clean, high-quality, natural ingredients. The design should establish a bold, masculine, minimalist identity that can later extend to products like shaving gel and body wash.

Key Requirements

Create a primary logo for “Brel” and a core label for the 2 oz pomade jar (screw-top).

Use a clean, modern style — masculine, confident, and approachable (think Dorran’s, Velta, Northfield Kit).

Design for 1–2 color screen printing on solid jar colors (white, black, or navy).

Avoid gradients, foil, or embossing. Must work in black & white.

Provide: vector logo, mockup of the 2 oz jar, color palette (CMYK/RGB/HEX), and font specs.

Winning design may lead to future projects (body wash, shave gel, skincare lines).

Font styles to use
Other font styles liked:
• We like the fonts and design concept in the attached mockup.

Requirements
Should not have
• We want to avoid too much writing or busy designs. We want to avoid having graphics/illustrations embedded in the logo if they will cause the brand to look less classy or sophisticated. We also want the design to look simple and all-American (e.g. Hollister and Vane, Pine Ledger, The KIM, etc). We’d like to give a Pellham & Royce vibe that feels classy and high end.

```html
<!DOCTYPE html>
<html lang="en">
<head>
<meta charset="UTF-8">
<title>Brel Hair Pomade Label</title>
<link href="https://fonts.googleapis.com/css2?family=Playfair+Display:wght@400;500;600&display=swap" rel="stylesheet">
<style>
  :root {
    --ink: #111111;
    --label: #ffffff;
    --backdrop: #f1f1f1;
    --edge: #dcdcdc;
  }
  html, body {
    margin: 0;
    padding: 0;
    width: 1200px;
    height: 1200px;
    overflow: hidden;
    background: var(--backdrop);
  }
  .canvas {
    width: 1200px;
    height: 1200px;
    display: flex;
    align-items: center;
    justify-content: center;
  }
  .label {
    width: 760px;
    height: 1000px;
    background: var(--label);
    border: 1px solid var(--edge);
    box-sizing: border-box;
    padding: 150px 0 0 130px;
    color: var(--ink);
    font-family: "Playfair Display", serif;
  }
  .brand-name {
    margin: 0;
    font-size: 290px;
    font-weight: 600;
    line-height: 0.8;
    letter-spacing: -4px;
    text-transform: lowercase;
  }
  .tagline {
    margin: 40px 0 0 70px;
    font-size: 62px;
    font-weight: 400;
    line-height: 1;
  }
  .product-name {
    margin: 120px 0 0 70px;
    font-size: 64px;
    font-weight: 500;
    line-height: 1;
  }
  .specs {
    margin: 140px 0 0 150px;
    font-size: 26px;
    font-weight: 400;
    line-height: 1.45;
  }
  .specs p { margin: 0; }
  .specs .net-weight { font-size: 30px; }
</style>
</head>
<body>
  <main class="canvas">
    <section class="label">
      <h1 class="brand-name">Brel</h1>
      <p class="tagline">Fresh &amp; Clean</p>
      <h2 class="product-name">Hair Pomade</h2>
      <div class="specs">
        <p class="hold">Medium Hold - Matte Finish</p>
        <p class="net-weight">Net WT 2 oz (57g)</p>
      </div>
    </section>
  </main>
</body>
</html>
```